Promotional business a5 Notepad design

I am looking for a custom a5 notepad design as a promotional item to give away to customers etc.
Attached will be a desk planner we had designed feel free to use as a reference.
We want the notepad to have lines running horizontal not squares like the desk planner example.

Industry/Entity Type

Hydraulic / industrial

Colors

Designer to choose colors to be used in the design.

```html
<!DOCTYPE html>
<html lang="en">
<head>
<meta charset="utf-8">
<title>Meridian Hose &amp; Couplings – A5 Notepad</title>
<link rel="stylesheet" href="https://fonts.googleapis.com/css2?family=Arimo:wght@400;700&display=swap">
<style>
  :root {
    --backdrop: #a1a1a3;
    --paper: #ffffff;
    --brand-blue: #132dbf;
    --swoosh: #161616;
    --ink: #1a1a1a;
    --rule: #b4b4b4;
    --header-text: #ffffff;
  }
  * { box-sizing: border-box; margin: 0; padding: 0; }
  html, body {
    width: 1200px;
    height: 900px;
    overflow: hidden;
    background: var(--backdrop);
    font-family: "Arimo", Arial, sans-serif;
  }
  .notepad {
    position: absolute;
    left: 325px;
    top: 60px;
    width: 550px;
    height: 780px;
    background: var(--paper);
    overflow: hidden;
  }
  .header-wave {
    position: absolute;
    left: 0;
    top: 0;
    width: 550px;
    height: 140px;
  }
  .contact {
    position: absolute;
    right: 26px;
    top: 21px;
    text-align: right;
    color: var(--header-text);
    font-size: 11.5px;
    line-height: 13px;
  }
  .contact-line {
    display: flex;
    justify-content: flex-end;
    align-items: center;
    gap: 4px;
  }
  .contact-icon { width: 8px; height: 8px; fill: var(--header-text); }
  .service-area { margin-top: 6px; }
  .brand {
    position: absolute;
    left: 38px;
    top: 59px;
    display: flex;
    align-items: center;
    gap: 8px;
  }
  .brand-mark {
    width: 40px;
    height: 40px;
    border-radius: 50%;
    background: var(--brand-blue);
    flex: none;
  }
  .brand-name {
    font-size: 15px;
    line-height: 17px;
    font-weight: 700;
    color: var(--brand-blue);
    letter-spacing: 0.3px;
  }
  .writing-lines {
    position: absolute;
    left: 38px;
    top: 158.5px;
    width: 474px;
    height: 561px;
    background: repeating-linear-gradient(
      to bottom,
      var(--rule) 0,
      var(--rule) 1px,
      transparent 1px,
      transparent 29.47px
    );
  }
</style>
</head>
<body>
  <main class="notepad">
    <svg class="header-wave" viewBox="0 0 550 140" aria-hidden="true">
      <path fill="var(--brand-blue)" d="M0 0 H550 V111 C470 118 385 100 305 68 C215 32 105 4 0 10 Z"/>
      <path fill="var(--swoosh)" d="M0 24 C120 2 230 22 322 66 C402 104 472 124 550 112 V126 C462 136 390 121 310 86 C222 48 120 24 0 42 Z"/>
      <path fill="none" stroke="var(--swoosh)" stroke-width="1.5" d="M82 30 C170 25 250 42 312 70"/>
    </svg>

    <div class="contact">
      <p class="contact-line">08 5550 1427
        <svg class="contact-icon" viewBox="0 0 10 10"><path d="M2 0.5 L3.6 2.6 L2.8 3.6 C3.5 5 4.8 6.3 6.3 7.1 L7.3 6.3 L9.5 7.9 L8.3 9.5 C4.3 9 1 5.7 0.5 1.7 Z"/></svg>
      </p>
      <p class="contact-line">0400 555 318
        <svg class="contact-icon" viewBox="0 0 10 10"><path d="M2 0.5 L3.6 2.6 L2.8 3.6 C3.5 5 4.8 6.3 6.3 7.1 L7.3 6.3 L9.5 7.9 L8.3 9.5 C4.3 9 1 5.7 0.5 1.7 Z"/></svg>
      </p>
      <p class="contact-line">hello@meridianhose.com.au
        <svg class="contact-icon" viewBox="0 0 10 10"><path d="M0 2 H10 V8 H0 Z M0.8 2.6 L5 5.6 L9.2 2.6" stroke="var(--brand-blue)" stroke-width="0.8"/></svg>
      </p>
      <p class="service-area">Servicing The Adelaide<br>Metropolitan Area</p>
    </div>

    <div class="brand">
      <span class="brand-mark"></span>
      <span class="brand-name">MERIDIAN HOSE<br>&amp; COUPLINGS</span>
    </div>

    <div class="writing-lines"></div>
  </main>
</body>
</html>
```